Multi-Line Insurance PPC Landing Page - Conversion optimized.

We have a PPC landing page used for the general population to get an insurance quote through an agent's site.

We'd like to improve the page for PPC traffic, make it more conversion friendly.

Site should be a single long page.

We will dynamically change the form and headlines on the page depending on what insurance "line" is being called. ie, Lift, Auto, Home, Business.

The enclosed AI file has all of the raw elements we need. We're looking to enhance the design and conversion ability.

Target Market(s)

General public needed insurance services.

Industry/Entity Type

Insurance Broker

Number of Pages Required

1 page

Font styles to use
Sans Serif

Requirements
Must have
• Form, agent picture, name, address.

```html
<!DOCTYPE html>
<html lang="en">
<head>
<meta charset="utf-8">
<title>Insurance Agent – Get a Quote</title>
<link href="https://fonts.googleapis.com/css2?family=Open+Sans:wght@400;600;700&display=swap" rel="stylesheet">
<style>
:root{
  --blue:#1f5fb0;
  --blue-dark:#174b8e;
  --green:#2f7d1e;
  --green-dark:#25661a;
  --text:#444;
  --muted:#777;
  --line:#d8d8d8;
  --grey-bg:#ececec;
  --white:#fff;
}
*{box-sizing:border-box;margin:0;padding:0}
html,body{width:1200px;height:2184px;overflow:hidden}
body{font-family:"Open Sans",Arial,sans-serif;color:var(--text);background:var(--white);position:relative}
.section{position:absolute;left:0;width:1200px}
.container{position:absolute;left:120px;width:960px}

/* header */
.site-header{top:0;height:88px}
.brand{position:absolute;left:8px;top:22px;font-size:32px;font-weight:700;color:var(--blue)}
.header-phone{position:absolute;right:0;top:20px;display:flex;align-items:center;gap:10px}
.header-phone .label{font-size:12px;color:var(--muted)}
.header-phone .number{font-size:22px;font-weight:700;color:var(--blue)}

/* hero */
.hero{top:88px;height:500px}
.hero-photo{position:absolute;inset:0;background:linear-gradient(120deg,#2a2d33 0%,#4e555e 45%,#8b8f93 70%,#3b3f46 100%)}
.hero-arrow{position:absolute;top:232px;width:34px;height:46px;background:rgba(200,200,200,.85);display:flex;align-items:center;justify-content:center}
.hero-arrow.prev{left:0}.hero-arrow.next{right:0}
.hero-caption{position:absolute;left:120px;top:222px;width:320px;padding:14px 22px 20px;background:rgba(20,20,20,.55)}
.hero-caption h1{font-size:36px;font-weight:700;color:var(--white);margin-bottom:14px}
.btn{display:inline-block;background:var(--green);color:var(--white);font-weight:700;text-transform:uppercase;border:0;font-family:inherit}
.hero-caption .btn{font-size:18px;padding:12px 22px}

/* lines */
.lines{top:548px;height:260px}
.line-cards{display:flex;gap:20px}
.line-card{width:225px;height:250px;background:var(--white);box-shadow:0 4px 14px rgba(0,0,0,.18);text-align:center;padding-top:78px;position:relative}
.line-icon{position:absolute;left:50%;top:-30px;margin-left:-58px;width:116px;height:116px;border-radius:50%;background:var(--blue);border:6px solid var(--white);box-shadow:0 2px 6px rgba(0,0,0,.2);display:flex;align-items:center;justify-content:center}
.line-card h3{font-size:26px;font-weight:600;color:#333;margin-top:22px}
.line-card p{font-size:13px;line-height:18px;color:var(--muted);padding:6px 24px 12px}
.line-card .btn{font-size:13px;padding:6px 16px}

/* quote */
.quote{top:868px;height:450px}
.quote-wrap{background:var(--grey-bg);height:420px;padding:14px}
.agent-card{position:absolute;left:14px;top:14px;width:340px;height:392px;background:var(--white);text-align:center;padding-top:26px}
.agent-photo{width:176px;height:176px;margin:0 auto;border-radius:50%;border:6px solid var(--blue);background:linear-gradient(160deg,#c7ccd2,#5d6470)}
.agent-name{font-size:22px;font-weight:600;color:#333;margin-top:18px}
.agent-phone{display:flex;justify-content:center;align-items:center;gap:8px;font-size:17px;font-weight:600;color:#333;margin-top:10px}
.agent-address{font-size:15px;color:#555;margin-top:14px;line-height:20px}
.quote-form{position:absolute;left:374px;top:14px;width:572px;height:392px;background:var(--white);padding:16px 22px}
.quote-form h2{font-size:24px;font-weight:600;color:var(--blue);border-bottom:1px solid var(--line);padding-bottom:10px}
.quote-form h2 span{color:#333}
.form-grid{display:grid;grid-template-columns:1fr 1fr;column-gap:36px;row-gap:14px;margin-top:16px}
.field label{display:block;font-size:13px;color:#444;margin-bottom:4px}
.input{height:28px;border:1px solid var(--line);background:var(--white);font-size:12px;color:#999;padding:6px 8px;position:relative}
.select::after{content:"";position:absolute;right:8px;top:11px;border:5px solid transparent;border-top-color:#888}
.dob{display:flex;gap:8px}.dob .input{flex:1}
.quote-form .btn{font-size:14px;padding:7px 22px;margin-top:16px}

/* about */
.about{top:1290px;height:150px;text-align:center}
.section-title{font-size:30px;font-weight:600;color:var(--blue)}
.section-title span{color:#333}
.about p{font-size:15px;line-height:24px;color:#555;margin-top:14px;padding:0 20px}

/* reviews */
.reviews{top:1460px;height:340px;background:var(--grey-bg)}
.reviews-head{position:absolute;left:0;width:1200px;top:24px;display:flex;justify-content:center;align-items:center;gap:28px}
.reviews-head::before,.reviews-head::after{content:"";position:absolute;top:50%;height:1px;background:#bbb;width:280px}
.reviews-head::before{left:180px}.reviews-head::after{right:180px}
.review-cards{top:96px;display:flex;gap:50px}
.review{width:455px;position:relative}
.review-box{background:var(--white);border:1px solid var(--line);height:150px;padding:20px 24px 0 54px;font-size:14px;line-height:21px;color:#666;position:relative}
.review-box .quote-mark{position:absolute;left:18px;top:6px;font-size:48px;color:#bbb;font-family:Georgia,serif}
.review-meta{display:flex;align-items:center;gap:20px;margin:-22px 0 0 18px;position:relative}
.avatar{width:82px;height:82px;border-radius:50%;border:4px solid var(--white);background:linear-gradient(160deg,#b9a08e,#4f4a48);box-shadow:0 1px 4px rgba(0,0,0,.25)}
.review-name{font-size:15px;font-weight:600;color:var(--green);margin-top:20px}

/* partners */
.partners{top:1850px;height:170px}
.partners .section-title{text-align:center}
.partner-row{position:absolute;top:66px;left:0;width:960px;height:82px;border:1px solid var(--line);border-radius:4px;display:flex;justify-content:space-around;align-items:center;padding:0 50px}
.partner-arrow{position:absolute;top:30px}
.partner-arrow.prev{left:-26px}.partner-arrow.next{right:-26px}
.partner{display:flex;align-items:center;gap:8px;font-size:22px;font-weight:700;color:#333}
.partner i{display:block;width:14px;height:14px;background:#333}

/* footer */
.site-footer{top:2040px;height:144px;background:var(--blue)}
.disclaimer{text-align:center;color:var(--white);padding:14px 120px 0}
.disclaimer h4{font-size:14px;font-weight:700;margin-bottom:4px}
.disclaimer p{font-size:12px;line-height:18px;opacity:.9}
.footer-bar{position:absolute;bottom:0;left:0;width:1200px;height:50px;background:var(--blue-dark)}
.footer-bar .copy{position:absolute;left:120px;top:17px;font-size:12px;color:var(--white)}
.footer-bar .brand-small{position:absolute;right:120px;top:8px;font-size:26px;font-weight:700;color:var(--white)}
</style>
</head>
<body>

<header class="section site-header">
  <div class="container" style="height:88px">
    <div class="brand">Insurance Agent</div>
    <div class="header-phone">
      <svg width="36" height="36" viewBox="0 0 24 24" aria-hidden="true"><path fill="#1f5fb0" d="M6.6 10.8c1.4 2.8 3.8 5.1 6.6 6.6l2.2-2.2c.3-.3.7-.4 1-.2 1.1.4 2.3.6 3.6.6.6 0 1 .4 1 1V20c0 .6-.4 1-1 1C10.6 21 3 13.4 3 4c0-.6.4-1 1-1h3.5c.6 0 1 .4 1 1 0 1.3.2 2.5.6 3.6.1.3 0 .7-.2 1l-2.3 2.2z"/></svg>
      <div><div class="label">Get a quick quote by phone</div><div class="number">(555) 014-2290</div></div>
    </div>
  </div>
</header>

<section class="section hero">
  <div class="hero-photo" role="img" aria-label="Hand holding a small model house with red roof on a dark background"></div>
  <div class="hero-arrow prev"><svg width="14" height="20" viewBox="0 0 14 20"><path d="M11 2 3 10l8 8" stroke="#fff" stroke-width="3" fill="none"/></svg></div>
  <div class="hero-arrow next"><svg width="14" height="20" viewBox="0 0 14 20"><path d="m3 2 8 8-8 8" stroke="#fff" stroke-width="3" fill="none"/></svg></div>
  <div class="hero-caption">
    <h1>Home Insurance</h1>
    <span class="btn">Get a Quote!</span>
  </div>
</section>

<section class="section lines">
  <div class="container line-cards">
    <div class="line-card">
      <div class="line-icon"><svg width="56" height="56" viewBox="0 0 56 56" aria-hidden="true"><g fill="#fff"><rect x="8" y="20" width="20" height="18" rx="2"/><rect x="12" y="10" width="12" height="12" fill="none" stroke="#fff" stroke-width="3"/><rect x="32" y="8" width="4" height="36"/><rect x="32" y="40" width="16" height="4"/><circle cx="14" cy="42" r="5"/><circle cx="27" cy="42" r="5"/></g></svg></div>
      <h3>Lift</h3>
      <p>Fast coverage quotes from local carriers you can trust.</p>
      <span class="btn">Get a Quote</span>
    </div>
    <div class="line-card">
      <div class="line-icon"><svg width="56" height="56" viewBox="0 0 56 56" aria-hidden="true"><g fill="#fff"><path d="M12 26l5-12h22l5 12v14H12z"/><rect x="12" y="38" width="8" height="8" rx="2"/><rect x="36" y="38" width="8" height="8" rx="2"/></g><path d="M19 25l3-7h12l3 7z" fill="#1f5fb0"/><circle cx="18" cy="32" r="3" fill="#1f5fb0"/><circle cx="38" cy="32" r="3" fill="#1f5fb0"/></svg></div>
      <h3>Auto</h3>
      <p>Fast coverage quotes from local carriers you can trust.</p>
      <span class="btn">Get a Quote</span>
    </div>
    <div class="line-card">
      <div class="line-icon"><svg width="56" height="56" viewBox="0 0 56 56" aria-hidden="true"><path fill="#fff" d="M28 8 6 28h7v18h11V34h8v12h11V28h7z"/></svg></div>
      <h3>Home</h3>
      <p>Fast coverage quotes from local carriers you can trust.</p>
      <span class="btn">Get a Quote</span>
    </div>
    <div class="line-card">
      <div class="line-icon"><svg width="56" height="56" viewBox="0 0 56 56" aria-hidden="true"><path fill="none" stroke="#fff" stroke-width="4" d="M21 18v-5h14v5"/><rect x="8" y="18" width="40" height="28" rx="3" fill="#fff"/><rect x="8" y="29" width="40" height="3" fill="#1f5fb0"/></svg></div>
      <h3>Business</h3>
      <p>Fast coverage quotes from local carriers you can trust.</p>
      <span class="btn">Get a Quote</span>
    </div>
  </div>
</section>

<section class="section quote">
  <div class="container quote-wrap">
    <div class="agent-card">
      <div class="agent-photo" role="img" aria-label="Portrait photo of the agent in a dark suit"></div>
      <div class="agent-name">Marcus Hale - Agent</div>
      <div class="agent-phone"><svg width="18" height="18" viewBox="0 0 24 24" aria-hidden="true"><path fill="#1f5fb0" d="M6.6 10.8c1.4 2.8 3.8 5.1 6.6 6.6l2.2-2.2c.3-.3.7-.4 1-.2 1.1.4 2.3.6 3.6.6.6 0 1 .4 1 1V20c0 .6-.4 1-1 1C10.6 21 3 13.4 3 4c0-.6.4-1 1-1h3.5c.6 0 1 .4 1 1 0 1.3.2 2.5.6 3.6.1.3 0 .7-.2 1l-2.3 2.2z"/></svg>(555) 014-2291</div>
      <div class="agent-address">418 Harbor Lane<br>Fairview, CA 90210</div>
    </div>
    <div class="quote-form">
      <h2>Get An Instant <span>Insurance Quote.</span></h2>
      <div class="form-grid">
        <div class="field"><label>First Name:</label><div class="input"></div></div>
        <div class="field"><label>Height/Weight:</label><div class="input"></div></div>
        <div class="field"><label>Sex:</label><div class="input select">Select</div></div>
        <div class="field"><label>Tobacco Use:</label><div class="input select">Select</div></div>
        <div class="field"><label>Date of Birth:</label><div class="dob"><div class="input select">Month</div><div class="input select">Day</div><div class="input select">Year</div></div></div>
        <div class="field"><label>Phone:</label><div class="input"></div></div>
        <div class="field"><label>Current Health:</label><div class="input select">Select</div></div>
        <div class="field"><label>Email:</label><div class="input"></div></div>
      </div>
      <span class="btn">Submit</span>
    </div>
  </div>
</section>

<section class="section about">
  <div class="container">
    <h2 class="section-title">About <span>Insurance Agent</span></h2>
    <p>Our agency helps families and businesses compare coverage from leading carriers in one simple visit. We explain every option in plain words, find the discounts you qualify for, and stay with you when it is time to file a claim. Tell us what you need today and we will send a clear, no-pressure quote within one business day.</p>
  </div>
</section>

<section class="section reviews">
  <div class="reviews-head">
    <svg width="14" height="20" viewBox="0 0 14 20"><path d="M11 2 3 10l8 8" stroke="#333" stroke-width="3" fill="none"/></svg>
    <h2 class="section-title">Our <span>Customer Review</span></h2>
    <svg width="14" height="20" viewBox="0 0 14 20"><path d="m3 2 8 8-8 8" stroke="#333" stroke-width="3" fill="none"/></svg>
  </div>
  <div class="container review-cards" style="position:absolute">
    <div class="review">
      <div class="review-box"><span class="quote-mark">“</span>Switching our home and auto policies took one short call. The agent found savings we never knew about and answered every question with real patience. Highly recommended.</div>
      <div class="review-meta"><div class="avatar" role="img" aria-label="Customer portrait photo"></div><div class="review-name">Mr Owen Castell</div></div>
    </div>
    <div class="review">
      <div class="review-box"><span class="quote-mark">“</span>When our shop flooded, the claim was handled in days, not weeks. Friendly service, clear answers and fair pricing every single year we have been with them.</div>
      <div class="review-meta"><div class="avatar" role="img" aria-label="Customer portrait photo"></div><div class="review-name">Mr Owen Castell</div></div>
    </div>
  </div>
</section>

<section class="section partners">
  <div class="container" style="height:170px">
    <h2 class="section-title">Insurance <span>Company</span></h2>
    <div class="partner-row">
      <svg class="partner-arrow prev" width="14" height="20" viewBox="0 0 14 20"><path d="M11 2 3 10l8 8" stroke="#1f5fb0" stroke-width="3" fill="none"/></svg>
      <div class="partner"><i></i>Brightledger</div>
      <div class="partner">Meadowline</div>
      <div class="partner">NORTHAX</div>
      <div class="partner">Vaultwell</div>
      <div class="partner">Keystone Tech</div>
      <svg class="partner-arrow next" width="14" height="20" viewBox="0 0 14 20"><path d="m3 2 8 8-8 8" stroke="#1f5fb0" stroke-width="3" fill="none"/></svg>
    </div>
  </div>
</section>

<footer class="section site-footer">
  <div class="disclaimer">
    <h4>Disclaimer</h4>
    <p>Quotes are estimates based on the details you provide and may change after review by the carrier. Coverage is subject to policy terms, conditions and exclusions. Availability varies by state.</p>
  </div>
  <div class="footer-bar">
    <div class="copy">© 2015 Insurance Agent. All Rights Reserved</div>
    <div class="brand-small">Insurance Agent</div>
  </div>
</footer>

</body>
</html>
```